Ward Compass Business Card Design*

We need a business card design for our company Ward Compass. Our company is specialized in providing online consulting services regarding medical institutions, hospitals and doctors. We work with patients worldwide looking to choose between healthcare providers. We have a website you may use as a reference, where we list doctors and clinics worldwide. So we target Medical providers as well as patients worldwide.
Target Market(s)
Medical Providers and patients around the world
Industry/Entity Type
Medical
Contact Information for Business Card
Salwa Kettani
CEO
+90 612 348 2175
info@wardcompass.example
www.wardcompass.example
14 Annakhil 7 H.R.B. Rabat, Morocco
Requirements
Must have
- Company logo/name on one full side, personal info and smaller logo and company name on the other side.
Nice to have
- Smart and elegant design

```html
<!DOCTYPE html>
<html lang="en">
<head>
<meta charset="utf-8">
<title>Ward Compass Business Card</title>
<link rel="stylesheet" href="https://fonts.googleapis.com/css2?family=Montserrat:wght@300;400;600;700&display=swap">
<style>
  :root {
    --brand-blue: #2ea5d8;
    --band-blue: #34a6da;
    --navy: #1f3a6e;
    --ink-grey: #4a4d52;
    --soft-grey: #7b7e83;
    --paper: #ffffff;
    --backdrop: #1d1f22;
  }
  * { box-sizing: border-box; margin: 0; padding: 0; }
  html, body {
    width: 1200px; height: 823px; overflow: hidden;
    background: var(--backdrop);
    font-family: "Montserrat", Arial, sans-serif;
  }
  .canvas {
    position: relative; width: 1200px; height: 823px;
    display: flex; align-items: center; justify-content: center; gap: 50px;
  }
  .card {
    position: relative; width: 540px; height: 310px; overflow: hidden;
    box-shadow: 0 10px 28px rgba(0,0,0,.55);
  }
  /* Front side */
  .card--front { background: var(--brand-blue); }
  .front-brand {
    position: absolute; left: 96px; top: 128px;
    display: flex; align-items: center; gap: 18px;
    color: var(--paper);
  }
  .brand-dot {
    width: 54px; height: 54px; border-radius: 50%;
    border: 8px solid var(--paper);
  }
  .front-brand__name {
    font-weight: 400; font-size: 33px; letter-spacing: 3px; text-transform: uppercase;
  }
  /* Back side */
  .card--back { background: var(--paper); }
  .contact-band {
    position: absolute; left: 116px; top: 196px; width: 330px; height: 84px;
    background: var(--band-blue);
  }
  .back-brand {
    position: absolute; right: 30px; top: 150px;
    display: flex; align-items: center; gap: 8px;
  }
  .back-brand .brand-dot { width: 34px; height: 34px; border: 5px solid var(--navy); }
  .back-brand__name { font-weight: 600; font-size: 14px; color: var(--navy); }
  .person {
    position: absolute; left: 40px; top: 62px;
  }
  .person__name { font-size: 22px; letter-spacing: .5px; line-height: 1; }
  .person__first { font-weight: 700; color: var(--brand-blue); }
  .person__last { font-weight: 300; color: var(--ink-grey); }
  .person__role { font-size: 11px; font-weight: 400; color: var(--ink-grey); margin-top: 3px; margin-left: 18px; }
  .company { position: absolute; left: 66px; top: 116px; font-size: 10.5px; color: var(--ink-grey); line-height: 1.35; }
  .company__name { font-weight: 700; color: var(--navy); font-size: 12px; }
  .contact-list {
    position: absolute; left: 140px; top: 208px; list-style: none;
    color: var(--paper); font-size: 11px; line-height: 20px;
  }
  .contact-list li { display: flex; align-items: center; gap: 10px; }
  .contact-list svg { width: 11px; height: 11px; fill: none; stroke: var(--paper); stroke-width: 1.6; }
</style>
</head>
<body>
<main class="canvas">
  <section class="card card--front" aria-label="Front of card">
    <div class="front-brand">
      <span class="brand-dot"></span>
      <span class="front-brand__name">Ward Compass</span>
    </div>
  </section>

  <section class="card card--back" aria-label="Back of card">
    <div class="contact-band"></div>
    <div class="back-brand">
      <span class="brand-dot"></span>
      <span class="back-brand__name">Ward Compass</span>
    </div>
    <div class="person">
      <p class="person__name"><span class="person__first">SALWA</span> <span class="person__last">KETTANI</span></p>
      <p class="person__role">CEO</p>
    </div>
    <div class="company">
      <p class="company__name">Ward Compass</p>
      <p>14 Annakhil 7 H.R.B.</p>
      <p>Rabat, Morocco</p>
    </div>
    <ul class="contact-list">
      <li><svg viewBox="0 0 12 12"><path d="M2 1.5l2 .2.8 2.3-1.2.9a6 6 0 0 0 3.5 3.5l.9-1.2 2.3.8.2 2A1 1 0 0 1 9.5 11 8.5 8.5 0 0 1 1 2.5a1 1 0 0 1 1-1z"/></svg>+90 612 348 2175</li>
      <li><svg viewBox="0 0 12 12"><rect x="1" y="2.5" width="10" height="7"/><path d="M1 2.5l5 4 5-4"/></svg>info@wardcompass.example</li>
      <li><svg viewBox="0 0 12 12"><circle cx="6" cy="6" r="5"/><path d="M1 6h10M6 1c-2.5 3-2.5 7 0 10M6 1c2.5 3 2.5 7 0 10"/></svg>www.wardcompass.example</li>
    </ul>
  </section>
</main>
</body>
</html>
```